Venture Capital firm needs modern business cards

We are a Venture Capital firm within financial services/Asset management. The industry generally has basic business cards with black, blue and maybe green/yellow design elements.
Our firm has a four-colour swoosh logo. We are based in London and want to stand out, just a little bit!, from the crowd. Our company is called LORV Investments and the 'C' stands for collaboration thus using makerswarm is a natural portal for our business card design competition. Our logo came via makerswarm too!
We use 'Venture Partner in Asset Management' as our tagline and this is Trademark registered. We operate in a conservative industry and we should not overstep our mark. The logo is colorful as it is and therefore the rest of the design should not be too fanciful.
The objective is twofold: make our logo element stick and memorable with our audience, whilst representing a conservative yet young image.
Updates
The Business Card obviously needs a field for Name, Surname, Job Title, Adress fields: Street, City, Postcode, Country, telefone and cell number, website address, etc.
We have uploaded the ai file. We trust that these are OK. If not, please advise.
Reason: We have have been busy with a client engagement. We will set the project as Guaranteed in return for the troubles we cause. Apologies for the confusion.
Thank you all for these great and creative design suggestions. The team is very happy with a number of your ideas! We will be in touch tomorrow to give individual feedback before the project closes on Friday. We look forward to working with some of you to narrow down your creations. Thank you, LORV Investments team.
All,
Target Market(s)
Financial Services Professionals, Investors, Media, 35-70 years, mainly male, well educated
Industry/Entity Type
Conservative
Requirements
Must have
- We must make use of our logo and potential tagline 'Venture Partner in Asset Management' as we are establishing a new Brand and new company in the market.
We can use 'LORV', 'LORV Investments', and 'LORV Investments'+tagline 'Venture Partner in Asset Management' or simply the four-colour swoosh plus the name of the company as part of the text. (see files)
All design elements are available in black or grey-scale if required. (grey scale swoosh attached).
Due to regulation we must have the following wording on the card in small print 'LORV Investments is an Appointed Representative of Bramwell Holdings Partnership Limited, which is authorised by the Monetary Oversight Board'.
Nice to have
- We would consider designs that make use of different printing techniques such embossing/debossing, UV spot etc.
We attach our colour palette in the files section for your reference.
Should not have
- The font we use for our company name is 'EXO' so do not use a font style that clashes with the corporate fonts, please.
Do not use other design elements than the ones we provide in the file library as part of this project.

```html
<!DOCTYPE html>
<html lang="en">
<head>
<meta charset="utf-8">
<title>LORV Investments – Business Card</title>
<link rel="stylesheet" href="https://fonts.googleapis.com/css2?family=Exo:wght@500&family=Arimo:wght@400;700&display=swap">
<style>
  :root {
    --canvas: #e7e7e8;
    --stage: #dcdbd9;
    --footer: #ffffff;
    --card-white: #ffffff;
    --ink-dark: #3a3a3c;
    --ink-muted: #6d6e71;
    --teal: #86cfd6;
    --green: #6bbd45;
    --icon-yellow: #f3d43a;
    --text-on-card: #ffffff;
    --brand-dot: #3a3a3c;
  }
  * { box-sizing: border-box; margin: 0; padding: 0; }
  html, body { width: 1200px; height: 555px; overflow: hidden; }
  body {
    position: relative;
    background: var(--footer);
    font-family: "Arimo", Arial, sans-serif;
    color: var(--ink-dark);
  }

  .stage {
    position: absolute; left: 0; top: 0;
    width: 782px; height: 510px;
    background: var(--stage);
  }
  .presentation {
    position: absolute; left: 782px; top: 0;
    width: 418px; height: 510px;
    background: var(--canvas);
  }

  /* Card base */
  .card {
    position: absolute;
    width: 31.7em; height: 18.2em;
    border-radius: 0.9em;
    box-shadow: 0 1.2em 1.2em -0.9em rgba(0,0,0,0.35);
  }

  /* Front */
  .card-front {
    font-size: 10px;
    left: 838px; top: 65px;
    background: var(--card-white);
  }
  .brand {
    position: absolute; left: 9.2em; top: 6.6em;
    display: flex; align-items: flex-start; gap: 1em;
  }
  .brand-dot {
    width: 3.4em; height: 3.4em; border-radius: 50%;
    background: var(--brand-dot);
    margin-top: 0.4em;
  }
  .brand-text { display: flex; flex-direction: column; }
  .brand-name {
    font-family: "Exo", sans-serif; font-weight: 500;
    font-size: 4.6em; line-height: 0.9; color: var(--ink-dark);
    letter-spacing: 0.01em;
  }
  .tagline {
    margin-top: 0.5em;
    font-size: 0.6em; color: var(--ink-muted);
    white-space: nowrap;
  }

  /* Back */
  .card-back { color: var(--text-on-card); }
  .card-back--teal { font-size: 10px; left: 838px; top: 294px; background: var(--teal); }
  .card-back--green { font-size: 17px; left: 121px; top: 100px; background: var(--green); }
  .card-back--green .icon { color: var(--icon-yellow); }

  .holder {
    position: absolute; right: 1.8em; top: 1.6em;
    text-align: right;
  }
  .holder-name { font-size: 1.1em; line-height: 1.25; }
  .holder-title { font-size: 1em; line-height: 1.2; }

  .contacts {
    position: absolute; left: 1em; bottom: 0.8em; right: 0.8em;
  }
  .contact-row {
    display: flex; gap: 2em;
    font-size: 1em; line-height: 1.45;
  }
  .contact { display: flex; align-items: center; gap: 0.55em; white-space: nowrap; }
  .icon { width: 1.15em; height: 1.15em; flex: none; color: var(--text-on-card); }
  .fine-print {
    margin-top: 0.25em;
    font-size: 0.74em; line-height: 1.35;
  }
  .fine-line { display: block; white-space: nowrap; }

  .note {
    position: absolute; left: 18px; top: 528px;
    font-size: 14px; color: #222;
  }
  .note strong { font-weight: 700; }
</style>
</head>
<body>
  <svg width="0" height="0" style="position:absolute" aria-hidden="true">
    <defs>
      <symbol id="i-phone" viewBox="0 0 16 16"><path d="M3 1.5l2.5 0 1.2 3.2-1.6 1.1c.9 1.9 2.3 3.3 4.2 4.2l1.1-1.6 3.2 1.2v2.5c0 .8-.7 1.4-1.5 1.4C6.6 13.2 2.8 9.4 1.6 3 1.5 2.2 2.2 1.5 3 1.5z" fill="none" stroke="currentColor" stroke-width="1.2" stroke-linejoin="round"/></symbol>
      <symbol id="i-mobile" viewBox="0 0 16 16"><rect x="4.5" y="1" width="7" height="14" rx="1.2" fill="none" stroke="currentColor" stroke-width="1.2"/><line x1="7" y1="12.6" x2="9" y2="12.6" stroke="currentColor" stroke-width="1.2"/></symbol>
      <symbol id="i-mail" viewBox="0 0 16 16"><rect x="1.5" y="3.5" width="13" height="9" fill="none" stroke="currentColor" stroke-width="1.2"/><path d="M1.5 3.5L8 9l6.5-5.5" fill="none" stroke="currentColor" stroke-width="1.2"/></symbol>
      <symbol id="i-globe" viewBox="0 0 16 16"><circle cx="8" cy="8" r="6.5" fill="none" stroke="currentColor" stroke-width="1.2"/><ellipse cx="8" cy="8" rx="2.8" ry="6.5" fill="none" stroke="currentColor" stroke-width="1.1"/><line x1="1.5" y1="8" x2="14.5" y2="8" stroke="currentColor" stroke-width="1.1"/></symbol>
      <symbol id="i-home" viewBox="0 0 16 16"><path d="M1.5 8L8 2l6.5 6M3.5 6.5V14h9V6.5M6.5 14v-4h3v4" fill="none" stroke="currentColor" stroke-width="1.2" stroke-linejoin="round"/></symbol>
    </defs>
  </svg>

  <main>
    <section class="stage">
      <article class="card card-back card-back--green">
        <div class="holder">
          <p class="holder-name">Martin Hale</p>
          <p class="holder-title">Chairman</p>
        </div>
        <div class="contacts">
          <div class="contact-row">
            <span class="contact"><svg class="icon"><use href="#i-phone"/></svg>+1 (800) 555-0142</span>
            <span class="contact"><svg class="icon"><use href="#i-mobile"/></svg>+1 (800) 555-0142</span>
          </div>
          <div class="contact-row">
            <span class="contact"><svg class="icon"><use href="#i-mail"/></svg>martin@lorvinvestments.com</span>
            <span class="contact"><svg class="icon"><use href="#i-globe"/></svg>www.lorvinvestments.com</span>
          </div>
          <div class="contact-row">
            <span class="contact"><svg class="icon"><use href="#i-home"/></svg>17 Harrow Lane, 22 Copeland Square, London, United Kingdom</span>
          </div>
          <p class="fine-print"><span class="fine-line">‘LORV Investments is an Appointed Representative of Bramwell Holdings</span><span class="fine-line">Partnership Limited, which is authorised by the Monetary Oversight Board’.</span></p>
        </div>
      </article>
    </section>

    <section class="presentation">
    </section>

    <article class="card card-front">
      <div class="brand">
        <span class="brand-dot"></span>
        <div class="brand-text">
          <span class="brand-name">lorv</span>
          <p class="tagline">Venture Partner in Asset Management</p>
        </div>
      </div>
    </article>

    <article class="card card-back card-back--teal">
      <div class="holder">
        <p class="holder-name">Martin Hale</p>
        <p class="holder-title">Chairman</p>
      </div>
      <div class="contacts">
        <div class="contact-row">
          <span class="contact"><svg class="icon"><use href="#i-phone"/></svg>+1 (800) 555-0142</span>
          <span class="contact"><svg class="icon"><use href="#i-mobile"/></svg>+1 (800) 555-0142</span>
        </div>
        <div class="contact-row">
          <span class="contact"><svg class="icon"><use href="#i-mail"/></svg>martin@lorvinvestments.com</span>
          <span class="contact"><svg class="icon"><use href="#i-globe"/></svg>www.lorvinvestments.com</span>
        </div>
        <div class="contact-row">
          <span class="contact"><svg class="icon"><use href="#i-home"/></svg>17 Harrow Lane, 22 Copeland Square, London, United Kingdom</span>
        </div>
        <p class="fine-print"><span class="fine-line">‘LORV Investments is an Appointed Representative of Bramwell Holdings</span><span class="fine-line">Partnership Limited, which is authorised by the Monetary Oversight Board’.</span></p>
      </div>
    </article>

    <p class="note">• Note : <strong>Two colour options</strong></p>
  </main>
</body>
</html>
```